Community Management Company in need of WordPress templates for website redesign

We are a community association management company providing services to homeowner associations (HOAs), condominium associations, cooperatives, municipal utility districts, luxury high-rises and large master-planned communities within the Real Estate category.

We are looking to do a refresh of our site with newly-designed pages that are compatible with WordPress and can be uploaded to a domain with little complications.

We are interested in first having a landing page designed based on a specific audience and call to actions as described in the design brief file attached to this design project and pasted below:
Design Brief for HavenStead Website Refresh

General Details:
Company Name: HavenStead
Business Location: Carrollton, TX – HQ
Current website: www.havenstead-example.com

Overview:

We are looking to for a refresh of our site with newly-designed pages that are compatible with WordPress and can be uploaded to a domain with little complications.

Our target audience / target market:
HOA and Association Board Members, Real Estate Builders & Developers, Residents and Homeowners, Vendors, Potential Business Partners

Project scope:
Create a landing page template with the target audience of HOA Board Members who are prospects of HavenStead
The goal of the landing page is to have them fill out the proposal form by having the page take them from our “why” message to our “how” and “what” messages so they are compelled to fill out the form. The new landing page needs to drive that behavior.
Our messages will include the following

Why messages:
• Because you deserve an exceptional community
• Because you and your residents deserve an exceptional lifestyle
• Because your community matters
• Because your residents matter
• Exceptional Community. Managed
• Exceptional Lifestyle. Delivered
How/What messages:

With over 25 years of experience, HavenStead provides exceptional community management solutions with the transparency and visibility your community deserves. Our fully integrated services are provided at competitive prices with the best people, best practices, and best cloud-based and mobile app technology.

Our team is made up of the industry’s leading experts equipped to answer your questions quickly. Our team includes: certified managers, degreed and certified accountants, experienced, multi-lingual customer service representatives, technology staff and industry executives. We perform industry leading best practices, on behalf of the communities we serve, ensuring you receive the highest level support, guidance and tools to assist in performing your fiduciary duties. With our proprietary, cloud-based and mobile app technology, pertinent community information is at your fingertips. You will be empowered to manage the business affairs of your community anytime, from any device, anywhere.

Our community management services include personalized onsite management, portfolio management, full-service community maintenance services, community management for builders and property developers, and Virtual CAM (Community Association Manager) management.

Our community communication services include cloud-based board, resident, closing, and attorney portals and mobile app technology, providing the transparency and visibility into the business affairs that your community deserves. In addition, we provide several communication tools to keep homeowners and residents informed via our community website, newsletter and event services.

HavenStead, one of the largest and fastest growing community management companies, is proud to provide exceptional services to hundreds of community associations from under 50 units to over 7,000 units in Arizona, California, Colorado, Florida, Georgia, Louisiana, Nevada, North Carolina, Oregon, Texas and Washington, including homeowner associations (HOAs), condominium associations, cooperatives, luxury high-rises, municipal utility districts and large master-planned communities.

Other page elements: additional content block/placeholders for:
• Link to Service description and technology pages
• Link to Mobile Apps page
• Request a proposal form fill content block
• Find an office form fill content block and link to local page upon completion of search via zip or state
• Contact us content block with information to include phone, email, fax, etc. and link to contact us landing page

Template Elements:
Files will also be uploaded including:
• Logo
• Colors
• Sales PPT for their reference

Please see attached design brief (file #4), logos (file #2&3), colors & branding standards (file #5) and a sales PPT deck (file #1) geared towards the audience for your reference.
Updates

Reason: I am extending the deadline by one week to give everyone a chance to provide updates based on the feedback and submissions. Thank you for all of your efforts. I look forward to seeing all of your designs.

Reason: Good day everyone, We are extending our deadline by one more week; so please continue to submit your designs and revisions. We look forward to seeing your work. Regards.

Thank you for all of your submissions.  I am in the process of getting votes tallied and should have some further information Tuesday of next week.

I am currently reviewing the votes and comments from the poll and will provide feedback within the next day; so please stay tuned.

We are conducting one more round of voting for the website refresh.  Once this is complete we will contact the finalists and make a selection shortly thereafter.  Thank you again for your participation.  Please stay tuned.

We are finalizing our 2nd poll and will request revisions, if appropriate.  Thank you.

Target Market(s)

HOA Board members per the design brief

Industry/Entity Type

Communication

Requirements
Must have
• focus on a landing page first; not the homepage design
Nice to have
• Please see design brief - File #4
Should not have
• home page elements for the time being.

```html
<!DOCTYPE html>
<html lang="en">
<head>
<meta charset="utf-8">
<title>HavenStead – Exceptional Community. Managed.</title>
<link href="https://fonts.googleapis.com/css2?family=Open+Sans:wght@400;600;700&display=swap" rel="stylesheet">
<style>
:root{
  --green:#4b8f3a;
  --green-dark:#3b7530;
  --teal:#1f7d8c;
  --teal-dark:#175f6b;
  --ink:#333b40;
  --muted:#6d767b;
  --line:#dfe3e5;
  --panel:rgba(28,36,40,.82);
  --footer:#2b3338;
  --footer-dark:#20272b;
  --bg:#ffffff;
}
*{box-sizing:border-box;margin:0;padding:0}
html,body{width:1200px;height:2224px;overflow:hidden}
body{font-family:"Open Sans",Arial,sans-serif;color:var(--ink);background:var(--bg);font-size:13px;line-height:1.6;position:relative}
.wrap{width:880px;margin:0 auto;position:relative}
.btn{background:var(--green);color:#fff;font-size:12px;font-weight:600;padding:0 16px;height:34px;display:inline-flex;align-items:center;white-space:nowrap}

/* header */
.site-header{height:132px}
.site-header .wrap{display:flex;justify-content:space-between;align-items:center;height:132px}
.brand{display:flex;align-items:center;gap:10px}
.brand-mark{width:14px;height:14px;background:var(--green)}
.brand-name{font-size:34px;font-weight:700;color:var(--green-dark);letter-spacing:-.5px}
.top-contact{display:flex;gap:22px;font-size:12px;color:var(--muted);align-items:center}
.top-contact span{display:flex;align-items:center;gap:6px}

/* nav */
.main-nav{background:var(--green);height:28px}
.main-nav ul{list-style:none;display:flex;height:28px}
.main-nav li{display:flex;align-items:center;padding:0 18px;color:#fff;font-size:11.5px;font-weight:600;white-space:nowrap}
.main-nav li.home{background:var(--green-dark);padding:0 16px}

/* hero */
.hero{position:relative;height:400px;background:linear-gradient(180deg,#9cc6e6 0%,#cfe3ef 45%,#8fbf5a 78%,#5f9a36 100%)}
.hero-photo{position:absolute;inset:0}
.hero-panel{position:absolute;left:592px;top:118px;width:400px;background:var(--panel);color:#fff;padding:24px 28px}
.hero-panel h2{font-size:19px;font-weight:600;line-height:1.35;margin-bottom:14px}
.hero-panel ul{list-style:none}
.hero-panel li{display:flex;align-items:center;gap:10px;font-size:13px;padding:4px 0}
.slide-arrow{position:absolute;top:180px;width:26px;height:40px;background:rgba(255,255,255,.75);display:flex;align-items:center;justify-content:center}
.slide-arrow.prev{left:30px}.slide-arrow.next{right:30px}

/* office finder */
.office-finder{margin-top:130px}
.office-finder .wrap{display:flex;height:150px;background:var(--teal)}
.finder-intro{width:420px;flex:none;background:var(--teal-dark);color:#fff;padding:32px 30px}
.finder-intro h3{font-size:23px;font-weight:400;white-space:nowrap}
.finder-intro p{font-size:12px;opacity:.85;margin-top:4px}
.finder-form{padding:32px 30px;color:#fff}
.finder-form label{font-size:12px;font-weight:600;display:block;margin-bottom:8px}
.finder-row{display:flex;gap:8px}
.finder-row .field{width:290px;height:34px;background:#fff}

/* welcome */
.welcome{margin-top:20px}
.welcome .wrap{display:flex;gap:24px}
.welcome-media{width:300px;height:180px;flex:none;background:linear-gradient(135deg,#1d4f8a,#2f78b8 60%,#1a3d6b)}
.welcome-text h2{font-size:21px;font-weight:400;margin-bottom:6px}
.welcome-text h2 b{color:var(--green);font-weight:700}
.welcome-text p{font-size:11.5px;color:var(--muted);margin-bottom:12px;line-height:1.55}

/* communities */
.section-title{font-size:22px;font-weight:400;margin-bottom:14px}
.section-title b{color:var(--green);font-weight:600}
.communities{margin-top:28px}
.community-grid{display:flex;gap:30px}
.community-card{width:273px}
.community-photo{height:208px}
.community-card dl{padding-top:12px;font-size:11.5px;color:var(--muted)}
.community-card .row{display:flex;gap:10px;padding:3px 0;border-bottom:1px solid var(--line)}
.community-card dt{color:var(--teal);font-weight:700;width:70px;flex:none}

/* bottom blocks */
.highlights{position:absolute;left:0;top:1568px;width:1200px}
.highlights .wrap{display:flex;gap:30px}
.block{width:425px}
.block-head{background:var(--green);color:#fff;font-size:14px;font-weight:600;padding:7px 16px}
.block-head.teal{background:var(--teal)}
.green-photo{height:268px;background:linear-gradient(180deg,#a8c98a,#5f8f3e 60%,#3f6b2c)}
.testimonial{background:#f3f5f6;height:268px;padding:28px 26px}
.testimonial blockquote{font-size:12.5px;color:var(--muted);border-left:3px solid var(--green);padding-left:14px}
.author{display:flex;align-items:center;gap:14px;margin-top:26px}
.avatar{width:60px;height:60px;background:#c9cfd2}
.author b{font-size:15px}
.author small{display:block;color:var(--muted);font-size:11px}

/* footer */
.site-footer{position:absolute;left:0;top:1912px;width:1200px;height:312px;background:var(--footer);color:#c8cfd2}
.footer-cols{display:flex;gap:40px;padding-top:34px}
.footer-cols .col{width:260px;font-size:11.5px}
.footer-cols h4{color:#fff;font-size:14px;font-weight:600;margin-bottom:12px;text-transform:uppercase;letter-spacing:.5px}
.footer-brand{font-size:26px;font-weight:700;color:#fff;display:flex;align-items:center;gap:8px;margin-bottom:10px}
.footer-brand i{width:12px;height:12px;background:var(--green)}
.nl-row{display:flex;margin-top:12px}
.nl-row .field{flex:1;height:32px;background:#fff;color:#999;font-size:11px;padding:7px 10px}
.nl-row .btn{height:32px;background:var(--teal)}
.footer-bar{position:absolute;bottom:0;left:0;width:1200px;height:40px;background:var(--footer-dark);font-size:11px}
.footer-bar .wrap{display:flex;justify-content:space-between;align-items:center;height:40px}
.socials{display:flex;gap:6px}
.socials i{width:20px;height:20px;border-radius:50%;background:#55636a;display:block}
</style>
</head>
<body>
<header class="site-header">
  <div class="wrap">
    <div class="brand"><span class="brand-mark"></span><span class="brand-name">HavenStead</span></div>
    <div class="top-contact">
      <span><svg width="12" height="12" viewBox="0 0 24 24"><path fill="#6d767b" d="M6.6 10.8a15 15 0 0 0 6.6 6.6l2.2-2.2c.3-.3.7-.4 1-.2 1.1.4 2.3.6 3.6.6.6 0 1 .4 1 1V20c0 .6-.4 1-1 1A17 17 0 0 1 3 4c0-.6.4-1 1-1h3.5c.6 0 1 .4 1 1 0 1.3.2 2.5.6 3.6.1.3 0 .7-.2 1z"/></svg>Call us : 800-555-0142</span>
      <span><svg width="13" height="10" viewBox="0 0 26 20"><rect x="1" y="1" width="24" height="18" fill="none" stroke="#6d767b" stroke-width="2"/><path d="M1 1l12 10L25 1" fill="none" stroke="#6d767b" stroke-width="2"/></svg>info@havenstead-example.com</span>
    </div>
  </div>
</header>

<nav class="main-nav">
  <div class="wrap">
    <ul>
      <li class="home"><svg width="15" height="13" viewBox="0 0 24 20"><path fill="#fff" d="M12 0L0 10h3v10h6v-6h6v6h6V10h3z"/></svg></li>
      <li>Request A Proposal</li><li>About Us</li><li>Services</li><li>Resident Services</li><li>Lakeside Sale Service</li><li>Contact Us</li>
    </ul>
  </div>
</nav>

<section class="hero">
  <div class="hero-photo" role="img" aria-label="Smiling family standing on a green lawn in front of a suburban home under a blue sky"></div>
  <div class="slide-arrow prev"><svg width="10" height="16" viewBox="0 0 10 16"><path d="M8 2L2 8l6 6" fill="none" stroke="#333" stroke-width="2"/></svg></div>
  <div class="slide-arrow next"><svg width="10" height="16" viewBox="0 0 10 16"><path d="M2 2l6 6-6 6" fill="none" stroke="#333" stroke-width="2"/></svg></div>
  <div class="hero-panel">
    <h2>Residents, Board Members, Closing Agents and Attorneys</h2>
    <ul>
      <li><svg width="14" height="14" viewBox="0 0 14 14"><circle cx="7" cy="7" r="7" fill="#4b8f3a"/><path d="M3.5 7l2.5 2.5 4.5-5" fill="none" stroke="#fff" stroke-width="1.6"/></svg>Resident Portal</li>
      <li><svg width="14" height="14" viewBox="0 0 14 14"><circle cx="7" cy="7" r="7" fill="#4b8f3a"/><path d="M3.5 7l2.5 2.5 4.5-5" fill="none" stroke="#fff" stroke-width="1.6"/></svg>Board Portal</li>
      <li><svg width="14" height="14" viewBox="0 0 14 14"><circle cx="7" cy="7" r="7" fill="#4b8f3a"/><path d="M3.5 7l2.5 2.5 4.5-5" fill="none" stroke="#fff" stroke-width="1.6"/></svg>Closing Portal</li>
      <li><svg width="14" height="14" viewBox="0 0 14 14"><circle cx="7" cy="7" r="7" fill="#4b8f3a"/><path d="M3.5 7l2.5 2.5 4.5-5" fill="none" stroke="#fff" stroke-width="1.6"/></svg>Attorney Portal</li>
    </ul>
  </div>
</section>

<section class="office-finder">
  <div class="wrap">
    <div class="finder-intro">
      <h3>Find &nbsp;a HavenStead Office</h3>
      <p>Because your community matters – find the HavenStead office nearest you by entering your zip code below.</p>
    </div>
    <div class="finder-form">
      <label>Zip Code</label>
      <div class="finder-row"><div class="field"></div><span class="btn">Submit</span></div>
    </div>
  </div>
</section>

<section class="welcome">
  <div class="wrap">
    <div class="welcome-media" role="img" aria-label="Blue banner photo with the word community"></div>
    <div class="welcome-text">
      <h2>Welcome to <b>HavenStead</b></h2>
      <p>Exceptional Community. Managed. Because you and your residents deserve an exceptional lifestyle, HavenStead brings over 25 years of experience, certified managers and cloud-based portals with the transparency your board deserves. We serve hundreds of associations in Arizona, California, Colorado, Florida, Georgia, Louisiana, Nevada, North Carolina, Oregon, Texas and Washington. Request a proposal today and see how we can serve your community.</p>
      <span class="btn">Read More</span>
    </div>
  </div>
</section>

<section class="communities">
  <div class="wrap">
    <h2 class="section-title">Client <b>Communities</b></h2>
    <div class="community-grid">
      <article class="community-card">
        <div class="community-photo" role="img" aria-label="Modern two-storey homes along a quiet street" style="background:linear-gradient(180deg,#b9d3ea,#e6e6e0 55%,#8a9a7a)"></div>
        <dl>
          <div class="row"><dt>Type</dt><dd>Single Family and Condominium</dd></div>
          <div class="row"><dt>Size</dt><dd>65 units</dd></div>
          <div class="row"><dt>Amenities</dt><dd>Park with playground, picnic area, walking paths, lovely grounds</dd></div>
        </dl>
      </article>
      <article class="community-card">
        <div class="community-photo" role="img" aria-label="Large villa with palm trees and landscaped lawn" style="background:linear-gradient(180deg,#a9cdea,#e9dcc4 50%,#6f9a4e)"></div>
        <dl>
          <div class="row"><dt>Type</dt><dd>Single Family and Condominium</dd></div>
          <div class="row"><dt>Size</dt><dd>65 units</dd></div>
          <div class="row"><dt>Amenities</dt><dd>Park with playground, picnic area, walking paths, lovely grounds</dd></div>
        </dl>
      </article>
      <article class="community-card">
        <div class="community-photo" role="img" aria-label="Resort-style home with a swimming pool at dusk" style="background:linear-gradient(180deg,#7fb2dd,#d9c7a6 50%,#3f9bc0)"></div>
        <dl>
          <div class="row"><dt>Type</dt><dd>Single Family and Condominium</dd></div>
          <div class="row"><dt>Size</dt><dd>65 units</dd></div>
          <div class="row"><dt>Amenities</dt><dd>Park with playground, picnic area, walking paths, lovely grounds</dd></div>
        </dl>
      </article>
    </div>
  </div>
</section>

<section class="highlights">
  <div class="wrap">
    <div class="block">
      <div class="block-head">Green Communities</div>
      <div class="green-photo" role="img" aria-label="Garden path lined with hedges and lawn"></div>
    </div>
    <div class="block">
      <div class="block-head teal">Testimonials</div>
      <div class="testimonial">
        <blockquote>“It is a pleasure to work with the people at HavenStead. Questions are answered and problems are solved quickly and confidently, without delay. The services are top-notch, and the people behind them make our community a great, stress-free place to live.”</blockquote>
        <div class="author">
          <div class="avatar" role="img" aria-label="Portrait of the testimonial author"></div>
          <div><b>President, Ridgeview Land</b><small>Board member</small></div>
        </div>
      </div>
    </div>
  </div>
</section>

<footer class="site-footer">
  <div class="wrap">
    <div class="footer-cols">
      <div class="col">
        <div class="footer-brand"><i></i>HavenStead</div>
        <p>Exceptional Lifestyle. Delivered. HavenStead provides community management for HOAs, condominiums and master-planned communities of every size.</p>
      </div>
      <div class="col">
        <h4>Address</h4>
        <p>1200 Meadow Park Drive, Suite 400<br>Carrollton, TX 75006</p>
        <p style="margin-top:10px">Call us: 800-555-0142 &nbsp;|&nbsp; Fax: 800-555-0143</p>
        <p style="margin-top:10px">info@havenstead-example.com</p>
      </div>
      <div class="col">
        <h4>Newsletter</h4>
        <p>Subscribe now to receive updates and news from our team right in your inbox each month.</p>
        <div class="nl-row"><div class="field">Enter Email</div><span class="btn">Sign Up</span></div>
      </div>
    </div>
  </div>
  <div class="footer-bar">
    <div class="wrap">
      <span>Copyright © 2016 HavenStead LLC. All rights reserved.</span>
      <div class="socials"><i></i><i></i><i></i><i></i><i></i></div>
      <span>Services | Residents | Lakeside Sale | Announcements | Contact</span>
    </div>
  </div>
</footer>
</body>
</html>
```